business card - Helicopter Flight Services, Flight School, etc.

We need a business card design for a new helicopter service.

We offer Helicopter Flight Services, Aerial Filming & Photography, Flight School, and Helicopter Tours. In that order.

Summit BladeAir, Inc.
Dennis Tollerby
SummitBladeair@Kestmail.com
626-418-7352

Based at the Brenwick Airport in Van Nuys, CA. The final design should communicate integrity and safety. Pictures or logos at your discretion.

Card back side - surprise me.

```html
<!DOCTYPE html>
<html lang="en">
<head>
<meta charset="utf-8">
<title>Summit BladeAir, Inc. — Business Card</title>
<link rel="stylesheet" href="https://fonts.googleapis.com/css2?family=Open+Sans:wght@400;600;700&display=swap">
<style>
  :root {
    --sky-blue: #4583c6;
    --card-white: #ffffff;
    --swoosh-grey: #9a9c9f;
    --ink-grey: #6f7275;
    --backdrop: #d9dadb;
  }
  * { box-sizing: border-box; margin: 0; padding: 0; }
  html, body {
    width: 1200px; height: 900px; overflow: hidden;
    background: var(--backdrop);
    font-family: "Open Sans", Arial, sans-serif;
  }
  .canvas {
    width: 1200px; height: 900px;
    display: flex; flex-direction: column;
    align-items: center; justify-content: center; gap: 40px;
  }
  .card {
    position: relative;
    width: 700px; height: 400px;
    overflow: hidden;
    box-shadow: 0 6px 18px rgba(0,0,0,.18);
  }

  /* Back side */
  .card-back {
    background: var(--sky-blue);
    color: var(--card-white);
    display: flex; flex-direction: column; align-items: center;
    padding-top: 92px;
  }
  .brand-mark {
    display: flex; align-items: center; gap: 14px;
  }
  .brand-dot {
    width: 34px; height: 34px; border-radius: 50%;
    border: 4px solid currentColor;
  }
  .brand-name {
    font-weight: 600; font-size: 34px; letter-spacing: 1px;
    line-height: 1.1; text-transform: uppercase;
  }
  .brand-suffix {
    font-weight: 600; font-size: 34px; letter-spacing: 1px;
    text-transform: uppercase;
  }
  .service-list {
    list-style: none; margin-top: 38px;
    text-align: center;
    font-weight: 700; font-size: 19px; line-height: 1.35;
  }

  /* Front side */
  .card-front { background: var(--card-white); }
  .card-front .front-shapes {
    position: absolute; inset: 0; width: 700px; height: 400px;
  }
  .front-brand {
    position: absolute; left: 28px; top: 150px; width: 280px;
    color: var(--sky-blue);
    display: flex; flex-direction: column; align-items: center; gap: 6px;
  }
  .front-brand .brand-mark { gap: 10px; }
  .front-brand .brand-dot { width: 24px; height: 24px; border-width: 3px; }
  .front-brand .brand-name { font-size: 24px; }
  .front-brand .brand-suffix { font-size: 24px; }
  .contact-block {
    position: absolute; right: 40px; top: 150px;
    color: var(--card-white); text-align: right;
  }
  .person-name {
    font-weight: 700; font-size: 26px; margin-bottom: 30px;
  }
  .contact-line {
    display: flex; justify-content: flex-end; align-items: center; gap: 12px;
    font-size: 19px; line-height: 1.5;
  }
  .contact-icon { width: 16px; height: 16px; fill: var(--card-white); }
</style>
</head>
<body>
<main class="canvas">

  <section class="card card-back" aria-label="Card back">
    <div class="brand-mark">
      <span class="brand-dot"></span>
      <span class="brand-name">Summit BladeAir</span>
    </div>
    <div class="brand-suffix" style="font-size:22px;margin-top:4px;">Inc.</div>
    <ul class="service-list">
      <li>Helicopter Flight Services,</li>
      <li>Aerial Filming &amp; Photography,</li>
      <li>Flight School,</li>
      <li>Helicopter Tours</li>
    </ul>
  </section>

  <section class="card card-front" aria-label="Card front">
    <svg class="front-shapes" viewBox="0 0 700 400" aria-hidden="true">
      <path d="M300 0 Q392 200 262 400 L246 400 Q362 200 280 0 Z" fill="var(--swoosh-grey)"/>
      <path d="M312 0 Q404 200 276 400 L700 400 L700 0 Z" fill="var(--sky-blue)"/>
    </svg>

    <div class="front-brand">
      <div class="brand-mark">
        <span class="brand-dot"></span>
        <span class="brand-name">Summit BladeAir</span>
      </div>
      <div class="brand-suffix" style="font-size:16px;">Inc.</div>
    </div>

    <div class="contact-block">
      <p class="person-name">Dennis Tollerby</p>
      <p class="contact-line">626-418-7352
        <svg class="contact-icon" viewBox="0 0 24 24" aria-label="Phone"><path d="M6.6 10.8a15 15 0 0 0 6.6 6.6l2.2-2.2a1 1 0 0 1 1-.25 11.4 11.4 0 0 0 3.6.57 1 1 0 0 1 1 1V20a1 1 0 0 1-1 1A17 17 0 0 1 3 4a1 1 0 0 1 1-1h3.5a1 1 0 0 1 1 1c0 1.25.2 2.45.57 3.6a1 1 0 0 1-.25 1z"/></svg>
      </p>
      <p class="contact-line">SummitBladeair@Kestmail.com
        <svg class="contact-icon" viewBox="0 0 24 24" aria-label="Email"><path d="M2 5h20v14H2z M3.5 6.5 12 13l8.5-6.5" fill="var(--card-white)" stroke="var(--sky-blue)" stroke-width="1.6"/></svg>
      </p>
    </div>
  </section>

</main>
</body>
</html>
```